Recruiting ad for Caregivers and Nurses

We need a few amazing, fun, catchy, creative recruiting ads for Caregivers and Nurses to care for homecare patients on the island of Oahu, in Hawaii. We are an in home care company called Palmer Homecare. Our care services are provided 24/7, so we need staff that can work days, nights, weekdays, weekends. We need catchy fun ads to entice caregivers and nurses to call our office to inquire about jobs available. Our patients age range is from babies to seniors. We need caregivers and nurses for basic patient care (bathing, dressing, ambulating, preparing meals, medication reminders, light housekeeping) and complex patients (oxygen, tube feeding, injections, vents, wound care). Here are some bullets to consider including:
*Full-time and Part-time Positions Available (days, nights, weekdays, weekends)
*Sign-On Bonus Programs Offered up to $500
*Refer a Friend Bonus Program
*Holiday Pay
*2 Health Plans to Choose from
*Island-Wide Locations
*All PPE Provided (masks, gloves, etc)
*401K Program
*Tuition Benefits

```html
<!DOCTYPE html>
<html lang="en">
<head>
<meta charset="utf-8">
<title>Palmer Homecare – We Are Hiring</title>
<link href="https://fonts.googleapis.com/css2?family=Arimo:wght@400;700&family=Tinos:wght@400;700&display=swap" rel="stylesheet">
<style>
  :root{
    --salmon:#f49a80;
    --ink:#231f20;
    --paper:#ffffff;
    --stage:#e9e6e2;
    --leaf:#9cc46a;
    --sky:#dfe8ee;
  }
  *{box-sizing:border-box;margin:0;padding:0}
  html,body{width:1200px;height:1200px;overflow:hidden;background:var(--stage)}
  .ad{position:absolute;left:40px;top:190px;width:1120px;height:820px;background:var(--paper);overflow:hidden;font-family:"Arimo",Arial,sans-serif;color:var(--ink)}
  .ad-shapes{position:absolute;inset:0}
  .badge{position:absolute;left:960px;top:12px;width:150px;text-align:center}
  .badge-num{font-weight:700;font-size:56px;color:var(--paper);letter-spacing:-2px;line-height:1}
  .badge-pill{display:inline-block;margin-top:6px;background:var(--paper);color:var(--ink);font-weight:700;font-size:20px;padding:3px 14px;border-radius:20px}
  .brand{position:absolute;left:690px;top:100px;width:230px;display:flex;flex-direction:column;align-items:center;gap:10px}
  .brand-mark{width:40px;height:40px;background:var(--ink)}
  .brand-name{font-weight:700;font-size:30px;color:var(--ink);white-space:nowrap}
  .headline{position:absolute;left:150px;top:100px;font-family:"Tinos","Times New Roman",serif;font-size:80px;font-weight:400;color:var(--ink);letter-spacing:1px;line-height:1.1;white-space:nowrap}
  .megaphone{position:absolute;left:50px;top:118px;width:88px;height:80px}
  .roles{position:absolute;left:150px;top:216px;background:var(--ink);color:var(--paper);font-size:30px;padding:12px 30px;border-radius:34px;letter-spacing:.5px}
  .perks{position:absolute;left:190px;top:296px;list-style:none;font-size:21px;line-height:25px}
  .perks li{height:36px;white-space:nowrap}
  .perks li:first-child{height:66px}
  .steps{position:absolute;left:90px;top:286px;width:40px;height:380px}
  .step{position:absolute;left:0;width:34px;height:34px;border-radius:50%;background:var(--salmon);color:var(--paper);font-family:"Tinos",serif;font-weight:700;font-size:19px;display:flex;align-items:center;justify-content:center}
  .step-line{position:absolute;left:16px;top:20px;width:2px;height:330px;background:var(--salmon)}
  .contact{position:absolute;inset:0;color:var(--paper)}
  .phone-icon{position:absolute;left:40px;top:748px;width:44px;height:44px;border-radius:8px;background:var(--salmon);display:flex;align-items:center;justify-content:center}
  .phone{position:absolute;left:100px;top:735px;font-size:40px;line-height:1.1}
  .web{position:absolute;left:420px;top:740px;font-size:28px;display:flex;align-items:center;gap:12px}
  .hours{position:absolute;left:100px;top:786px;font-size:20px}
  .hours strong{color:var(--salmon)}
</style>
</head>
<body>
<main class="ad">
  <svg class="ad-shapes" viewBox="0 0 1120 820" width="1120" height="820">
    <defs>
      <clipPath id="heart-clip">
        <path d="M930 660 C830 600 740 520 745 420 C750 330 840 300 900 360 C940 260 1060 250 1095 330 C1125 410 1060 540 930 660 Z"/>
      </clipPath>
      <linearGradient id="photo-tone" x1="0" y1="0" x2="0" y2="1">
        <stop offset="0" stop-color="var(--sky)"/>
        <stop offset=".55" stop-color="#f3f4f6"/>
        <stop offset="1" stop-color="var(--leaf)"/>
      </linearGradient>
    </defs>
    <circle cx="1035" cy="30" r="130" fill="var(--salmon)"/>
    <circle cx="1035" cy="30" r="108" fill="none" stroke="var(--paper)" stroke-width="4"/>
    <path d="M0 700 C300 690 560 680 760 640 C900 610 1020 560 1120 520 L1120 820 L0 820 Z" fill="var(--salmon)"/>
    <path d="M0 725 C300 715 560 705 770 668 C910 640 1030 595 1120 560 L1120 820 L0 820 Z" fill="var(--ink)"/>
    <g role="img" aria-label="Photo of a smiling caregiver hugging an elderly woman in a wheelchair in a park">
      <rect x="730" y="240" width="400" height="430" fill="url(#photo-tone)" clip-path="url(#heart-clip)"/>
    </g>
    <path d="M930 660 C830 600 740 520 745 420 C750 330 840 300 900 360 C940 260 1060 250 1095 330 C1125 410 1060 540 930 660 Z" fill="none" stroke="var(--salmon)" stroke-width="26"/>
  </svg>

  <div class="badge">
    <div class="badge-num">24/7</div>
    <div class="badge-pill">Services</div>
  </div>

  <div class="brand">
    <span class="brand-mark"></span>
    <span class="brand-name">Palmer Homecare</span>
  </div>

  <svg class="megaphone" viewBox="0 0 88 80" aria-hidden="true">
    <g fill="none" stroke="var(--salmon)" stroke-width="5" stroke-linejoin="round" stroke-linecap="round">
      <path d="M14 30 L60 10 L60 66 L14 46 Z"/>
      <path d="M14 30 L6 30 L6 46 L14 46"/>
      <path d="M22 50 L28 72 L38 70 L34 54"/>
      <path d="M72 26 L80 22 M74 38 L84 38 M72 50 L80 54"/>
    </g>
  </svg>
  <h1 class="headline">We Are Hiring</h1>
  <div class="roles">CAREGIVERS AND NURSES</div>

  <div class="steps" aria-hidden="true">
    <span class="step-line"></span>
    <span class="step" style="top:6px">1</span>
    <span class="step" style="top:72px">2</span>
    <span class="step" style="top:108px">3</span>
    <span class="step" style="top:144px">4</span>
    <span class="step" style="top:180px">5</span>
    <span class="step" style="top:216px">6</span>
    <span class="step" style="top:252px">7</span>
    <span class="step" style="top:288px">8</span>
    <span class="step" style="top:324px">9</span>
  </div>
  <ul class="perks">
    <li>Full-time and Part-time Positions Available (days, nights,<br>weekdays, weekends)</li>
    <li>Sign-On Bonus Programs Offered up to $500</li>
    <li>Refer a Friend Bonus Program</li>
    <li>Holiday Pay</li>
    <li>2 Health Plans to Choose from</li>
    <li>Island-Wide Locations</li>
    <li>All PPE Provided (masks, gloves, etc)</li>
    <li>401K Program</li>
    <li>Tuition Benefits</li>
  </ul>

  <div class="contact">
    <span class="phone-icon">
      <svg width="26" height="26" viewBox="0 0 24 24" aria-hidden="true"><path d="M6.6 10.8a15.1 15.1 0 0 0 6.6 6.6l2.2-2.2a1 1 0 0 1 1-.25 11.4 11.4 0 0 0 3.6.57 1 1 0 0 1 1 1V20a1 1 0 0 1-1 1A17 17 0 0 1 3 4a1 1 0 0 1 1-1h3.5a1 1 0 0 1 1 1c0 1.25.2 2.45.57 3.57a1 1 0 0 1-.25 1z" fill="var(--ink)"/></svg>
    </span>
    <span class="phone">808-555-0142</span>
    <span class="web">
      <svg width="26" height="26" viewBox="0 0 24 24" aria-hidden="true"><g fill="none" stroke="var(--salmon)" stroke-width="1.8"><circle cx="12" cy="12" r="10"/><ellipse cx="12" cy="12" rx="4.5" ry="10"/><path d="M2 12h20M4 6.5h16M4 17.5h16"/></g></svg>
      www.palmercare.com
    </span>
    <p class="hours"><strong>Business Hours</strong> - Mo, Tu, We, Th, Fr - 8:30am – 5:00pm</p>
  </div>
</main>
</body>
</html>
```